GJ & DW Fencing Pty Ltd

We already have an existing logo created by Pixel Harbour however we have restructured to a company. We would like someone to add Pty Ltd to our business name please.

Colors

Designer to choose only greyscale colors for use in the design.

```html
<!DOCTYPE html>
<html lang="en">
<head>
<meta charset="utf-8">
<title>GJ &amp; DW Fencing Pty Ltd – Business Card</title>
<link rel="stylesheet" href="https://fonts.googleapis.com/css2?family=Lato:wght@400;900&display=swap">
<style>
  :root {
    --backdrop: #3b3b3b;
    --paper: #ffffff;
    --ink: #111111;
    --card-black: #0d0d0d;
    --rule: #222222;
    --shadow: rgba(0,0,0,0.45);
  }
  * { margin: 0; padding: 0; box-sizing: border-box; }
  html, body {
    width: 1200px; height: 866px; overflow: hidden;
    background: var(--backdrop);
    font-family: "Lato", sans-serif;
  }
  .stage {
    position: relative; width: 1200px; height: 866px;
    display: flex; align-items: center; justify-content: center; gap: 60px;
  }
  .card {
    position: relative; width: 520px; height: 297px;
    box-shadow: 0 10px 24px var(--shadow);
  }
  .card--front { background: var(--paper); color: var(--ink); }
  .card--back { background: var(--card-black); color: var(--paper); }

  .contact-list {
    position: absolute; left: 34px; top: 150px;
    list-style: none; font-size: 15px; line-height: 1;
  }
  .contact-list li { display: flex; align-items: center; gap: 9px; margin-bottom: 8px; }
  .contact-icon { width: 18px; height: 18px; flex: none; }

  .wordmark {
    position: absolute; text-align: center;
    font-family: "Lato", sans-serif; font-weight: 900; letter-spacing: 0.5px;
  }
  .card--front .wordmark { right: 40px; top: 118px; width: 230px; color: var(--ink); }
  .card--back .wordmark { left: 50%; top: 50%; transform: translate(-50%, -50%); width: 260px; color: var(--paper); }
  .wordmark__initials { display: block; font-size: 40px; line-height: 1; }
  .wordmark__trade { display: block; font-size: 26px; line-height: 1.1; margin-top: 2px; }
  .wordmark__entity {
    display: block; font-size: 10px; letter-spacing: 3px; margin-top: 6px;
    border-top: 1px solid currentColor; border-bottom: 1px solid currentColor;
    padding: 3px 0; width: 130px; margin-left: auto; margin-right: auto;
  }
</style>
</head>
<body>
<main class="stage">
  <section class="card card--front" aria-label="Business card front">
    <ul class="contact-list">
      <li>
        <svg class="contact-icon" viewBox="0 0 18 18" aria-hidden="true"><circle cx="9" cy="9" r="9" fill="#111"/><path d="M5.5 6.2c0 3.5 2.8 6.3 6.3 6.3l1-1.4-1.8-1.1-.9.8c-1-.5-1.7-1.2-2.2-2.2l.8-.9-1.1-1.8z" fill="#fff"/></svg>
        <span>048 5219374 (DAN)</span>
      </li>
      <li>
        <svg class="contact-icon" viewBox="0 0 18 18" aria-hidden="true"><circle cx="9" cy="9" r="9" fill="#111"/><rect x="4.5" y="6" width="9" height="6.5" fill="none" stroke="#fff" stroke-width="1"/><path d="M4.5 6 9 9.6 13.5 6" fill="none" stroke="#fff" stroke-width="1"/></svg>
        <span>gjdwfencing@postmail.com</span>
      </li>
      <li>
        <svg class="contact-icon" viewBox="0 0 18 18" aria-hidden="true"><circle cx="9" cy="9" r="9" fill="#111"/><path d="M9 4.2a3 3 0 0 0-3 3c0 2.3 3 6 3 6s3-3.7 3-6a3 3 0 0 0-3-3z" fill="#fff"/><circle cx="9" cy="7.2" r="1.1" fill="#111"/></svg>
        <span>PO Box 418 Harlow WA 6502</span>
      </li>
    </ul>
    <div class="wordmark">
      <span class="wordmark__initials">GJ &amp; DW</span>
      <span class="wordmark__trade">FENCING</span>
      <span class="wordmark__entity">PTY LTD</span>
    </div>
  </section>

  <section class="card card--back" aria-label="Business card back">
    <div class="wordmark">
      <span class="wordmark__initials">GJ &amp; DW</span>
      <span class="wordmark__trade">FENCING</span>
      <span class="wordmark__entity">PTY LTD</span>
    </div>
  </section>
</main>
</body>
</html>
```